I need the design of at least 200 icons to suit an app for iphones etc..

The icons can be used by anyone in martial arts or interested in martial arts to text amongst one another similar to emoticons. It is just a fun app to have on your phone.
I do not have a business/product or service.

1: all the colored belts for karate, white , orange , yellow, blue, purple, green, brown and black.... all to look tied around the waist.
2. I need a person figure wearing a white karate uniform and then add that person wearing all the different colored belts. So 8 people in all with the above 8 colored belt designs.
3. I need the same person icon design in a black karate uniform ..... same as a (2)
4. I need the same person icon design in a blue karate uniform with all belt colors as in (2)
5. I need icons of all weapons ,samurai sword, nunchakus , bo, sai (three tipped weapon) Kama (handle with blade on end)
6. I would like some icons of karate man holding the different weapons. This character be only in white uniform with black belt.
7. I would like a karate man icon dressed like a ninja in black with cover on face like a ninja.
8. icons of karate man doing kicks in different positions high kick, low kick , middle kick. maybe some jumping kick positions also
9. icons of little ninja man doing kicks in different positions.
10. animated word designs for Bam, Pow, smash, kapow Keeei,kowabunga, Shazam, Knockout, crash, shatter, demolish, destroy, exterminate,wipeout in at least 3 different fonts and colours per word.
11. Icon pics of , a bomb, atom bomb smoke, ninja throwing star.
12. All country flags. Australia Japan korea USA brazil, China , Englan , etc etc

hopefully i can get about 200 at least different icons that will suit Plimvexors for app store.
Updates

I have updated my payment to guaranteed and increased the budget....lets do this

I have updated my project. I am pretty sure that if i have at least 200 icons that will be sufficient. Thank you for your patience. 

I have increased the prize payment for this project to allow for more interest an designs

Target Market(s)

youth, martial arts interested or practicing people....anyone

Industry/Entity Type

Business

Requirements
Must have
• good animation.at least 200 icons need not move. Same size icons as iphone app emoticons
Nice to have
• the ability to add more icons in future
Should not have
• No guns

```html
<!DOCTYPE html>
<html lang="en">
<head>
<meta charset="utf-8">
<title>Impact Words</title>
<link rel="stylesheet" href="https://fonts.googleapis.com/css2?family=Roboto+Mono:wght@700&display=swap">
<style>
  :root {
    --paper: #ffffff;
    --ink: #000000;
    --sky: #00aeef;
    --purple-light: #a95bd0;
    --purple-deep: #8a3fa8;
    --green-light: #4bd85a;
    --green-deep: #2eb34a;
  }
  html, body {
    margin: 0;
    padding: 0;
    width: 1200px;
    height: 519px;
    overflow: hidden;
    background: var(--paper);
  }
  .word-board {
    display: block;
    width: 1200px;
    height: 519px;
  }
  .impact-word {
    font-family: "Roboto Mono", monospace;
    font-weight: 700;
    font-size: 61px;
  }
  .impact-word--black { fill: var(--ink); }
  .impact-word--blue { fill: var(--sky); }
  .impact-word--purple { fill: url(#purpleFade); }
  .impact-word--green { fill: url(#greenFade); }
  .stop-purple-light { stop-color: var(--purple-light); }
  .stop-purple-deep { stop-color: var(--purple-deep); }
  .stop-green-light { stop-color: var(--green-light); }
  .stop-green-deep { stop-color: var(--green-deep); }
</style>
</head>
<body>
<svg class="word-board" viewBox="0 0 1200 519" xmlns="http://www.w3.org/2000/svg" role="img" aria-label="Martial arts impact words">
  <defs>
    <linearGradient id="purpleFade" x1="0" y1="0" x2="1" y2="0">
      <stop offset="0" class="stop-purple-light"/>
      <stop offset="0.7" class="stop-purple-deep"/>
      <stop offset="1" class="stop-purple-light"/>
    </linearGradient>
    <linearGradient id="greenFade" x1="0" y1="0" x2="1" y2="0">
      <stop offset="0" class="stop-green-light"/>
      <stop offset="0.65" class="stop-green-deep"/>
      <stop offset="1" class="stop-green-light"/>
    </linearGradient>
  </defs>

  <g class="word-row">
    <text class="impact-word impact-word--purple" x="159" y="116" textLength="108" lengthAdjust="spacingAndGlyphs">BAM</text>
    <text class="impact-word impact-word--black" x="343" y="116" textLength="109" lengthAdjust="spacingAndGlyphs">POW</text>
    <text class="impact-word impact-word--green" x="492" y="116" textLength="182" lengthAdjust="spacingAndGlyphs">SMASH</text>
    <text class="impact-word impact-word--black" x="714" y="116" textLength="181" lengthAdjust="spacingAndGlyphs">KAPOW</text>
  </g>

  <g class="word-row">
    <text class="impact-word impact-word--black" x="58" y="214" textLength="219" lengthAdjust="spacingAndGlyphs">SHAZAM</text>
    <text class="impact-word impact-word--blue" x="356" y="214" textLength="290" lengthAdjust="spacingAndGlyphs">KNOCKOUT</text>
    <text class="impact-word impact-word--black" x="688" y="214" textLength="181" lengthAdjust="spacingAndGlyphs">CRASH</text>
    <text class="impact-word impact-word--purple" x="910" y="214" textLength="254" lengthAdjust="spacingAndGlyphs">SHATTER</text>
  </g>

  <g class="word-row">
    <text class="impact-word impact-word--green" x="76" y="336" textLength="217" lengthAdjust="spacingAndGlyphs">KEEEII</text>
    <text class="impact-word impact-word--black" x="372" y="336" textLength="330" lengthAdjust="spacingAndGlyphs">KOWABUNGA</text>
    <text class="impact-word impact-word--blue" x="768" y="336" textLength="292" lengthAdjust="spacingAndGlyphs">DEMOLISH</text>
  </g>

  <g class="word-row">
    <text class="impact-word impact-word--black" x="108" y="450" textLength="257" lengthAdjust="spacingAndGlyphs">DESTROY</text>
    <text class="impact-word impact-word--purple" x="408" y="450" textLength="400" lengthAdjust="spacingAndGlyphs">ESTERMINATE</text>
    <text class="impact-word impact-word--black" x="887" y="450" textLength="255" lengthAdjust="spacingAndGlyphs">WIPEOUT</text>
  </g>
</svg>
</body>
</html>
```